Harbor Crestline (Business Card Design)

Need business cards designed. Something modern, chic, and sleek. Mabye the back of the card should be the navy blue that is in the logo and then just the logo on the back.

Target Market(s)

Those in the hotel, office, and renovation industry

Contact Information for Business Card

1. Logo 2. Dorian Fenwick 3. CEO/Founder 4. Phone: (833) HarbCre / (833) 427-2731 5. Email: dorian@theharborcrestline.com 6. Website: www.theharborcrestline.com

Font styles to use
Other font styles liked:
• Look at the logo font and base the font for everything else off of that.

Colors
0054AA
0677BA
7BADD7
CADEEF
E8F1F8

Requirements
Must have
• Colors that are associated in the logo
Nice to have
• Sleek modern clean and chic design.

```html
<!DOCTYPE html>
<html lang="en">
<head>
<meta charset="utf-8">
<title>Harbor Crestline — Business Card</title>
<link rel="stylesheet" href="https://fonts.googleapis.com/css2?family=Open+Sans:wght@400;600;700&display=swap">
<style>
  :root {
    --stage: #e9ebf0;
    --navy: #0b1846;
    --navy-deep: #081236;
    --navy-light: #2a3578;
    --violet-sheen: #8c8fc4;
    --gold: #c9a23a;
    --white: #ffffff;
    --text-soft: #e6e8f2;
  }
  * { margin: 0; padding: 0; box-sizing: border-box; }
  html, body { width: 1200px; height: 780px; overflow: hidden; }
  body {
    background: var(--stage);
    font-family: "Open Sans", Arial, sans-serif;
    display: flex;
    align-items: center;
    justify-content: center;
    gap: 40px;
  }
  .card {
    position: relative;
    width: 540px;
    height: 310px;
    background: var(--navy);
    border-radius: 6px;
    overflow: hidden;
    box-shadow: 0 10px 28px rgba(8, 18, 54, 0.28);
  }

  /* Front */
  .front__mark-area {
    position: absolute;
    left: 34px;
    top: 34px;
    width: 170px;
    height: 150px;
    background: linear-gradient(110deg, var(--navy-deep) 0%, var(--navy-light) 60%, var(--violet-sheen) 100%);
    opacity: 0.75;
  }
  .front__content {
    position: absolute;
    right: 44px;
    top: 34px;
    text-align: right;
    color: var(--white);
  }
  .brand {
    display: flex;
    align-items: center;
    justify-content: flex-end;
    gap: 10px;
    font-weight: 600;
    font-size: 25px;
    letter-spacing: 0.04em;
    color: var(--white);
  }
  .brand__square {
    width: 18px;
    height: 18px;
    background: var(--gold);
  }
  .person__name {
    margin-top: 20px;
    font-weight: 700;
    font-size: 27px;
    line-height: 1.1;
    color: var(--gold);
  }
  .person__title {
    font-size: 15px;
    color: var(--white);
    margin-top: 2px;
  }
  .address {
    margin-top: 12px;
    font-size: 12.5px;
    line-height: 1.45;
    color: var(--text-soft);
    font-style: normal;
  }
  .contact-list {
    list-style: none;
    margin-top: 8px;
    font-size: 12.5px;
    line-height: 1.55;
    color: var(--text-soft);
  }
  .contact-list li {
    display: flex;
    align-items: center;
    justify-content: flex-end;
    gap: 7px;
  }
  .contact-list svg { width: 12px; height: 12px; flex: none; }
  .front__tab {
    position: absolute;
    right: 0;
    top: 110px;
    width: 20px;
    height: 52px;
    background: var(--gold);
  }

  /* Back */
  .back__pattern {
    position: absolute;
    inset: 0;
    background: linear-gradient(135deg, var(--navy-deep) 0%, var(--navy) 45%, var(--navy-light) 80%, var(--violet-sheen) 120%);
  }
  .back__brand {
    position: absolute;
    right: 40px;
    bottom: 34px;
    display: flex;
    align-items: center;
    gap: 8px;
    font-weight: 600;
    font-size: 15px;
    letter-spacing: 0.05em;
    color: var(--white);
  }
  .back__brand .brand__square { width: 11px; height: 11px; }
</style>
</head>
<body>

  <section class="card card--front" aria-label="Business card front">
    <div class="front__mark-area" role="img" aria-label="Large embossed brand symbol in navy with violet sheen"></div>
    <div class="front__tab"></div>
    <div class="front__content">
      <div class="brand"><span class="brand__square"></span>Harbor Crestline</div>
      <h1 class="person__name">Dorian Fenwick</h1>
      <p class="person__title">CEO/Founder</p>
      <address class="address">4120 Meridian Way<br>Suite 2200, Eastfield, MD 21090</address>
      <ul class="contact-list">
        <li>(833) HarbCre / (833) 427-2731
          <svg viewBox="0 0 24 24" aria-hidden="true"><path fill="#c9a23a" d="M6.6 10.8a15 15 0 0 0 6.6 6.6l2.2-2.2a1 1 0 0 1 1-.25 11.4 11.4 0 0 0 3.6.57 1 1 0 0 1 1 1V20a1 1 0 0 1-1 1A17 17 0 0 1 3 4a1 1 0 0 1 1-1h3.5a1 1 0 0 1 1 1c0 1.25.2 2.45.57 3.57a1 1 0 0 1-.25 1z"/></svg>
        </li>
        <li>www.theharborcrestline.com
          <svg viewBox="0 0 24 24" aria-hidden="true"><circle cx="12" cy="12" r="9" fill="none" stroke="#c9a23a" stroke-width="2.4"/><path d="M3 12h18M12 3c3 3.5 3 14.5 0 18M12 3c-3 3.5-3 14.5 0 18" fill="none" stroke="#c9a23a" stroke-width="1.8"/></svg>
        </li>
        <li>dorian@theharborcrestline.com
          <svg viewBox="0 0 24 24" aria-hidden="true"><rect x="2" y="5" width="20" height="14" rx="1.5" fill="#c9a23a"/><path d="M3 6l9 7 9-7" fill="none" stroke="#0b1846" stroke-width="1.8"/></svg>
        </li>
      </ul>
    </div>
  </section>

  <section class="card card--back" aria-label="Business card back">
    <div class="back__pattern" role="img" aria-label="Repeating small brand pattern on navy fading to a light violet sheen"></div>
    <div class="back__brand"><span class="brand__square"></span>Harbor Crestline</div>
  </section>

</body>
</html>
```